Mobile Fitness snd Therapy Business Card Design

I need a business card designed for my mobile fitness and therapy business.

Please view the images that I have uploaded. I like the simplicity of the design that I have attached. I adapted it with my information

Target Market(s)

Those seeking personal training, injury rehabilitation or massage therapy.

Industry/Entity Type

Business

Contact Information for Business Card

Derek Fulham - MSc, CAT(C), RMT, CSCS, Pn2
e-mail: derek@vantrelo.com
website: www.vantrelo.com
instagram: @derek_fulham

Font styles to use
Sans Serif

Colors
3176b5
0355a3

Requirements
Must have
• "Contact us to receive a FREE assessment"
• Services offered:
• Personal Training
• Golf Fitness
• Injury Rehab
• Massage Therapy
• Yoga
Nice to have
• Consistent colours with brand
• - Dark Blue: #232837
• - Blue: #5096f0
• Consistent look/feel with the website: www.vantrelo.com

```html
<!DOCTYPE html>
<html lang="en">
<head>
<meta charset="utf-8">
<title>Vantrelo Business Card</title>
<link href="https://fonts.googleapis.com/css2?family=Open+Sans:wght@400;600;700&display=swap" rel="stylesheet">
<style>
  :root {
    --backdrop: #c2c2c2;
    --card-white: #ffffff;
    --navy: #232837;
    --ink: #1f2330;
    --brand-blue: #5096f0;
  }
  * { margin: 0; padding: 0; box-sizing: border-box; }
  html, body {
    width: 1200px; height: 900px; overflow: hidden;
    background: var(--backdrop);
    font-family: "Open Sans", Arial, sans-serif;
  }
  .canvas { position: relative; width: 1200px; height: 900px; }

  .card { position: absolute; top: 306px; width: 440px; height: 272px; }
  .card-back { left: 149px; background: var(--card-white); color: var(--ink); }
  .card-front { left: 608px; background: var(--navy); color: #fff; }

  .edge-bar { position: absolute; top: 81px; height: 113px; background: var(--navy); }
  .edge-bar.left { left: 0; width: 11px; }
  .edge-bar.right { right: 0; width: 13px; }
  .divider { position: absolute; left: 220px; top: 81px; width: 5px; height: 113px; background: var(--navy); }

  .person { position: absolute; left: 30px; top: 84px; }
  .person-name { font-size: 17px; font-weight: 600; letter-spacing: 0.2px; line-height: 20px; }
  .credentials { font-size: 10.5px; margin-top: 4px; line-height: 13px; }
  .contact-list { list-style: none; margin-top: 13px; }
  .contact-list li { display: flex; align-items: center; font-size: 13px; line-height: 18px; }
  .contact-list svg { width: 9px; height: 9px; margin-right: 5px; flex: none; }

  .services { position: absolute; left: 285px; top: 84px; list-style: none; }
  .services li { font-size: 15px; line-height: 20px; }

  .call-to-action {
    position: absolute; left: 0; right: 0; top: 229px;
    text-align: center; font-size: 16px; font-weight: 600;
  }

  .brand-lockup { position: absolute; left: 0; right: 0; top: 98px; text-align: center; }
  .brand-name {
    display: inline-flex; align-items: center; gap: 14px;
    font-size: 44px; font-weight: 700; letter-spacing: 6px; line-height: 50px;
  }
  .brand-mark { width: 14px; height: 14px; background: var(--brand-blue); }
  .tagline { margin-top: 10px; font-size: 15px; font-weight: 700; letter-spacing: 3px; }
</style>
</head>
<body>
<div class="canvas">

  <section class="card card-back">
    <div class="edge-bar left"></div>
    <div class="person">
      <h1 class="person-name">DEREK FULHAM</h1>
      <p class="credentials">MSc, CAT(C), RMT, CSCS, Pn2</p>
      <ul class="contact-list">
        <li>
          <svg viewBox="0 0 10 10" aria-hidden="true"><rect x="0.5" y="1.5" width="9" height="7" fill="#232837"/><path d="M0.5 1.5 L5 5.5 L9.5 1.5" stroke="#fff" stroke-width="1" fill="none"/></svg>
          derek@vantrelo.com
        </li>
        <li>
          <svg viewBox="0 0 10 10" aria-hidden="true"><circle cx="5" cy="5" r="4.5" fill="#232837"/><path d="M0.5 5 H9.5 M5 0.5 C3 3 3 7 5 9.5 C7 7 7 3 5 0.5" stroke="#fff" stroke-width="0.7" fill="none"/></svg>
          www.vantrelo.com
        </li>
        <li>
          <svg viewBox="0 0 10 10" aria-hidden="true"><circle cx="5" cy="5" r="4" fill="none" stroke="#232837" stroke-width="1.4"/></svg>
          @derek_fulham
        </li>
      </ul>
    </div>
    <div class="divider"></div>
    <ul class="services">
      <li>Personal Training</li>
      <li>Golf Fitness</li>
      <li>Injury Rehab</li>
      <li>Massage Therapy</li>
      <li>Yoga</li>
    </ul>
    <div class="edge-bar right"></div>
    <p class="call-to-action">Contact us to receive a FREE assessment</p>
  </section>

  <section class="card card-front">
    <div class="brand-lockup">
      <div class="brand-name"><span>VANTRELO</span><span class="brand-mark"></span></div>
      <p class="tagline">NUTRITION - FITNESS - HEALTH</p>
    </div>
  </section>

</div>
</body>
</html>
```